KLV Plant Services

We are a heavy diesel mechanical business with additional air con certificates, remapping engine rebuilt

Contact Information for Business Card

Company Name, Director Name, Managing Director, Contact details, email and website

Font styles to use
Serif
Script

```html
<!DOCTYPE html>
<html lang="en">
<head>
<meta charset="utf-8">
<title>KLV Plant Services – Business Card</title>
<link href="https://fonts.googleapis.com/css2?family=Merriweather:wght@400;700&family=Great+Vibes&display=swap" rel="stylesheet">
<style>
  :root {
    --navy: #2b2a7a;
    --ink: #333333;
    --paper: #ffffff;
    --backdrop: #3b3431;
    --card-edge: #2a2880;
    --serif: "Merriweather", Georgia, serif;
    --script: "Great Vibes", "Brush Script MT", cursive;
  }
  * { box-sizing: border-box; margin: 0; padding: 0; }
  html, body {
    width: 1200px; height: 786px; overflow: hidden;
    background: var(--backdrop);
    font-family: var(--serif);
  }
  .canvas {
    position: relative; width: 1200px; height: 786px;
    display: flex; align-items: center; justify-content: center; gap: 40px;
  }
  .card {
    position: relative; width: 540px; height: 309px;
    background: var(--paper);
    box-shadow: 0 6px 0 var(--card-edge), 0 14px 30px rgba(0,0,0,.45);
  }

  /* contact side */
  .card-back .accent-bar {
    position: absolute; top: 20px; right: 0; width: 14px; height: 36px;
    background: var(--navy);
  }
  .card-back .person {
    position: absolute; top: 18px; right: 26px; text-align: right;
  }
  .person-name {
    color: var(--navy); font-family: var(--serif); font-weight: 700;
    font-size: 16px; letter-spacing: .6px; line-height: 1.2;
  }
  .person-role {
    color: var(--navy); font-family: var(--script);
    font-size: 19px; line-height: 1.1;
  }

  .wordmark {
    display: flex; align-items: center; gap: 8px;
    color: var(--navy); font-family: var(--serif); font-weight: 700;
    white-space: nowrap;
  }
  .wordmark .dot { border-radius: 50%; background: var(--navy); flex: none; }
  .card-back .wordmark { position: absolute; left: 28px; top: 112px; font-size: 16px; }
  .card-back .wordmark .dot { width: 14px; height: 14px; }

  .address {
    position: absolute; left: 32px; top: 160px;
    color: var(--ink); font-size: 12px; line-height: 1.5;
  }
  .contacts {
    position: absolute; left: 32px; bottom: 18px; list-style: none;
    color: var(--ink); font-size: 12px; line-height: 1.6;
  }
  .contacts li { display: flex; align-items: center; gap: 7px; }
  .contacts svg { width: 11px; height: 11px; fill: var(--navy); flex: none; }

  /* brand side */
  .card-front { display: flex; align-items: center; justify-content: center; }
  .card-front .wordmark { font-size: 30px; gap: 14px; }
  .card-front .wordmark .dot { width: 28px; height: 28px; }
</style>
</head>
<body>
<main class="canvas">
  <section class="card card-back" aria-label="Business card, contact side">
    <div class="accent-bar"></div>
    <div class="person">
      <p class="person-name">DANIEL HART</p>
      <p class="person-role">Managing Director</p>
    </div>
    <div class="wordmark"><span class="dot"></span><span>KLV Plant Services</span></div>
    <p class="address">Your address, City<br>State, Zip 1234</p>
    <ul class="contacts">
      <li><svg viewBox="0 0 24 24"><path d="M6.6 10.8a15 15 0 0 0 6.6 6.6l2.2-2.2a1 1 0 0 1 1-.25 11.4 11.4 0 0 0 3.6.57 1 1 0 0 1 1 1V20a1 1 0 0 1-1 1A17 17 0 0 1 3 4a1 1 0 0 1 1-1h3.5a1 1 0 0 1 1 1c0 1.25.2 2.45.57 3.57a1 1 0 0 1-.25 1z"/></svg>123 456 789</li>
      <li><svg viewBox="0 0 24 24"><path d="M2 5h20v14H2zM4 7v.5l8 5 8-5V7l-8 5z"/></svg>info@yourmail.com</li>
      <li><svg viewBox="0 0 24 24"><circle cx="12" cy="12" r="10"/></svg>www.yourwebsite.com</li>
    </ul>
  </section>

  <section class="card card-front" aria-label="Business card, brand side">
    <div class="wordmark"><span class="dot"></span><span>KLV Plant Services</span></div>
  </section>
</main>
</body>
</html>
```